Commercial Loan Originator Business Card (CHANGE COLORS SCHEME)

CHANGE COLOR SCHEME - SAME DESIGN

Name Marlene Agate
Title Commercial Loan Originator
Office (800) 417-2906 x68
Direct (240) 615-2043
Email freshgreens4life@quillbox.example

Name Dale Morrow
Office (800) 417-2906 x70
Direct (410) 392-5184
Email d.morthehomeguy@quillbox.example

Name Leonard Vasko
Office (800) 417-2906 x71
Direct (215) 463-0712
Email l.vasko41@quillbox.example

Name Gwen Halsey
Office (800) 417-2906 x
Direct (202) 548-1370
Email ghalsey63@quillbox.example

Name Mirna Ashby
Office (800) 417-2906 x72
Direct (240) 871-4526
Email tristatehomelending@quillbox.example

```html
<!DOCTYPE html>
<html lang="en">
<head>
<meta charset="utf-8">
<title>Mirna Ashby – Commercial Loan Originator</title>
<link rel="stylesheet" href="https://fonts.googleapis.com/css2?family=Montserrat:wght@400;500;800&display=swap">
<style>
  :root {
    --backdrop: #1c1c1c;
    --card-white: #ffffff;
    --brand-band: #1d5c4a;
    --name-ink: #17523f;
    --title-ink: #222428;
    --contact-ink: #ffffff;
    --portrait-dark: #2a2426;
    --portrait-mid: #5a3d35;
  }
  html, body {
    margin: 0;
    width: 1200px;
    height: 1059px;
    overflow: hidden;
    background: var(--backdrop);
  }
  .business-card {
    position: absolute;
    left: 50px;
    top: 217px;
    width: 1100px;
    height: 625px;
    border-radius: 26px;
    overflow: hidden;
    background: var(--card-white);
    font-family: "Montserrat", sans-serif;
  }
  .card-art {
    position: absolute;
    inset: 0;
  }
  .identity {
    position: absolute;
    left: 71px;
    top: 136px;
  }
  .identity-name {
    margin: 0;
    font-size: 50px;
    font-weight: 800;
    letter-spacing: 0.5px;
    line-height: 1;
    color: var(--name-ink);
    text-transform: uppercase;
  }
  .identity-title {
    margin: 8px 0 0;
    font-size: 30px;
    font-weight: 400;
    letter-spacing: 0.6px;
    color: var(--title-ink);
  }
  .contact-list {
    position: absolute;
    left: 68px;
    top: 400px;
    margin: 0;
    padding: 0;
    list-style: none;
  }
  .contact-item {
    display: flex;
    align-items: center;
    height: 42px;
    margin-bottom: 16px;
    font-size: 27px;
    font-weight: 400;
    letter-spacing: 0;
    white-space: nowrap;
    color: var(--contact-ink);
  }
  .contact-icon {
    width: 24px;
    height: 24px;
    margin-right: 12px;
    flex: none;
  }
</style>
</head>
<body>
  <div class="business-card">
    <svg class="card-art" width="1100" height="625" viewBox="0 0 1100 625">
      <defs>
        <linearGradient id="portraitTone" x1="0" y1="0" x2="0" y2="1">
          <stop offset="0" stop-color="#5a3d35"/>
          <stop offset="0.45" stop-color="#2a2426"/>
          <stop offset="1" stop-color="#2a2426"/>
        </linearGradient>
      </defs>
      <path class="band-wave" d="M0 313 Q 430 378 1100 186 L1100 625 L0 625 Z" fill="var(--brand-band)"/>
      <rect class="portrait" role="img" aria-label="Portrait photo of Mirna Ashby, seated, smiling, wearing a black ruffled top" x="710" y="118" width="380" height="507" rx="60" fill="url(#portraitTone)"/>
    </svg>

    <div class="identity">
      <h1 class="identity-name">Mirna Ashby</h1>
      <p class="identity-title">Commercial Loan Originator</p>
    </div>

    <ul class="contact-list">
      <li class="contact-item">
        <svg class="contact-icon" viewBox="0 0 24 24"><path fill="#fff" d="M6.6 10.8a15.1 15.1 0 0 0 6.6 6.6l2.2-2.2a1 1 0 0 1 1-.25 11.4 11.4 0 0 0 3.6.57 1 1 0 0 1 1 1V20a1 1 0 0 1-1 1A17 17 0 0 1 3 4a1 1 0 0 1 1-1h3.5a1 1 0 0 1 1 1c0 1.25.2 2.45.57 3.6a1 1 0 0 1-.25 1z"/></svg>
        (800) 417-2906 x72
      </li>
      <li class="contact-item">
        <svg class="contact-icon" viewBox="0 0 24 24"><rect x="6" y="2" width="12" height="20" rx="2" fill="none" stroke="#fff" stroke-width="2"/><circle cx="12" cy="18" r="1.3" fill="#fff"/></svg>
        (240) 871-4526
      </li>
      <li class="contact-item">
        <svg class="contact-icon" viewBox="0 0 24 24"><rect x="2" y="5" width="20" height="14" fill="#fff"/><path d="M2 5 L12 13 L22 5 M2 19 L9 11 M22 19 L15 11" fill="none" stroke="#1d5c4a" stroke-width="1.5"/></svg>
        tristatehomelending@quillbox.example
      </li>
    </ul>
  </div>
</body>
</html>
```